Create a business promotion flyer to leave in customer mailboxes. We are a bulk petroleum supplier, servicing any industry that requires diesel. Base in griffith NSW, servicing griffith area and surrounds.

Business Name - Terra Diesel
Fuel@terradiesel-example.com.au
Owen - 0491 570 362 ohartley@terradiesel-example.com.au
Liam - 0491 570 718 lprosser@terradiesel-example.com.au
Simon - 0491 570 905 skenway@terradiesel-example.com.au
Office 02 5550 1734

Bulk Fuel deliveries.
Oils & lubricants
Local Family owned business

```html
<!DOCTYPE html>
<html lang="en">
<head>
<meta charset="utf-8">
<title>Terra Diesel – Bulk Diesel Deliveries Flyer</title>
<link rel="stylesheet" href="https://fonts.googleapis.com/css2?family=Poppins:wght@700;800;900&family=Montserrat:wght@500;700&family=Oswald:wght@500&family=Open+Sans:wght@400;500&display=swap">
<style>
  :root {
    --red: #e3231c;
    --red-deep: #c51a14;
    --maroon: #8a1111;
    --ink: #111111;
    --stage: #9d9d9d;
    --white: #ffffff;
    --sky-top: #dce9f4;
    --sky-mid: #eef3f7;
    --ground: #cdc5bd;
  }
  * { box-sizing: border-box; margin: 0; padding: 0; }
  html, body { width: 1124px; height: 1200px; overflow: hidden; }
  body { background: var(--stage); position: relative; font-family: "Montserrat", sans-serif; }

  .flyer {
    position: absolute; left: 114px; top: 20px;
    width: 896px; height: 1160px; overflow: hidden;
  }
  .flyer-photo {
    position: absolute; inset: 0;
    background: linear-gradient(180deg, var(--sky-top) 0%, var(--sky-mid) 30%, #f3f5f7 52%, #c9d3dc 62%, #e4e6e8 75%, var(--ground) 100%);
  }
  .abs { position: absolute; }

  .brand-name {
    left: 0; width: 896px; top: 78px; text-align: center;
    font-family: "Poppins", sans-serif; font-weight: 800; font-size: 50px;
    color: var(--red); letter-spacing: 0.5px;
  }
  .headline {
    left: 0; width: 896px; top: 168px; text-align: center;
    font-family: "Poppins", sans-serif; font-weight: 900; font-size: 146px;
    line-height: 1; color: var(--red); letter-spacing: -2px;
  }
  .subhead {
    left: 0; width: 896px; top: 310px; text-align: center;
    font-family: "Poppins", sans-serif; font-weight: 800; font-size: 43px;
    color: var(--maroon); letter-spacing: -0.5px;
  }
  .moving {
    left: 0; width: 896px; top: 368px; text-align: center;
    font-family: "Poppins", sans-serif; font-weight: 800; font-size: 32px;
    color: var(--ink); letter-spacing: 37px; padding-left: 37px;
  }
  .divider { left: 195px; width: 506px; top: 425px; height: 1px; background: #9a9a9a; }
  .service-title {
    left: 0; width: 896px; top: 432px; text-align: center;
    font-family: "Poppins", sans-serif; font-weight: 800; font-size: 52px;
    color: var(--ink); letter-spacing: -1px;
  }
  .service-title .accent { color: var(--red); }

  .service-pill {
    left: 142px; top: 516px; width: 396px; height: 62px;
    background: var(--red); border-radius: 6px;
    display: flex; align-items: center; color: var(--white);
    font-family: "Montserrat", sans-serif; font-weight: 700; font-size: 18px; line-height: 1.05;
  }
  .service-item { display: flex; align-items: center; gap: 12px; flex: 1; padding-left: 22px; }
  .service-item + .service-item { border-left: 2px solid rgba(255,255,255,.85); height: 42px; }
  .service-item svg { flex: none; }

  .family-badge {
    left: 552px; top: 516px; display: flex; align-items: center; gap: 10px;
    font-family: "Oswald", sans-serif; font-weight: 500; font-size: 22px; line-height: 1.15; color: var(--ink);
  }

  .contact-list { left: 50px; top: 986px; display: flex; flex-direction: column; gap: 8px; }
  .contact {
    display: flex; align-items: center; width: 297px; height: 39px;
    background: var(--ink); border-radius: 20px; overflow: hidden;
    font-family: "Open Sans", sans-serif; font-size: 22px; color: var(--white);
  }
  .contact-name {
    background: var(--red); height: 100%; width: 120px; border-radius: 20px;
    display: flex; align-items: center; justify-content: space-between; padding: 0 4px 0 18px;
  }
  .phone-dot {
    width: 32px; height: 32px; border-radius: 50%; background: var(--white);
    display: flex; align-items: center; justify-content: center;
  }
  .contact-number { padding-left: 12px; letter-spacing: .3px; }

  .base-box {
    left: 385px; top: 985px; width: 461px; height: 86px;
    background: rgba(255,255,255,.55); border: 1.5px solid rgba(255,255,255,.9); border-radius: 6px;
    display: flex; align-items: center; gap: 32px; padding-left: 18px;
  }
  .region-map { width: 48px; height: 48px; background: var(--red); border-radius: 6px; }
  .base-title { font-weight: 700; font-size: 18px; color: var(--ink); }
  .base-sub { font-weight: 500; font-size: 21px; color: var(--ink); margin-top: 2px; }

  .web-row {
    left: 383px; top: 1092px; display: flex; gap: 26px;
    font-family: "Open Sans", sans-serif; font-size: 19px; color: var(--ink);
  }
  .web-item { display: flex; align-items: center; gap: 10px; }
  .web-icon {
    width: 24px; height: 24px; border-radius: 50%; background: var(--red);
    display: flex; align-items: center; justify-content: center;
  }
</style>
</head>
<body>
<main class="flyer">
  <div class="flyer-photo" role="img" aria-label="Photo of a white fuel tanker road train parked in front of a steel depot warehouse under a blue sky"></div>

  <div class="abs brand-name">Terra Diesel</div>
  <h1 class="abs headline">FUELING</h1>
  <div class="abs subhead">WHAT KEEPS OUR REGION</div>
  <div class="abs moving">MOVING</div>
  <div class="abs divider"></div>
  <h2 class="abs service-title"><span class="accent">Bulk Diesel</span> Deliveries</h2>

  <div class="abs service-pill">
    <div class="service-item">
      <svg width="30" height="34" viewBox="0 0 30 34" fill="none" stroke="#fff" stroke-width="2">
        <rect x="3" y="3" width="24" height="28"/><line x1="3" y1="10" x2="27" y2="10"/><line x1="3" y1="24" x2="27" y2="24"/>
        <path d="M15 12c-3 4-4 6-4 7.5a4 4 0 0 0 8 0c0-1.5-1-3.5-4-7.5z"/>
      </svg>
      <span>Oils &amp;<br>Lubricants</span>
    </div>
    <div class="service-item">
      <svg width="52" height="34" viewBox="0 0 52 34" fill="none" stroke="#fff" stroke-width="2">
        <rect x="2" y="6" width="32" height="18" rx="8"/><path d="M34 10h9l6 8v8H34z"/><line x1="2" y1="26" x2="49" y2="26"/>
        <circle cx="12" cy="28" r="4"/><circle cx="40" cy="28" r="4"/>
      </svg>
      <span>Petrol<br>Deliveries</span>
    </div>
  </div>

  <div class="abs family-badge">
    <svg width="50" height="56" viewBox="0 0 50 56" fill="#e3231c">
      <circle cx="30" cy="8" r="7"/><path d="M26.5 8l2.5 2.5 4.5-5" stroke="#fff" stroke-width="2" fill="none"/>
      <circle cx="18" cy="24" r="4"/><circle cx="30" cy="22" r="4"/><circle cx="42" cy="24" r="4"/>
      <path d="M12 36a6 6 0 0 1 12 0zM24 34a6 6 0 0 1 12 0zM36 36a6 6 0 0 1 12 0z"/>
      <path d="M2 44l10-4h14l8-3 2 3-10 6-14 2-8 4z"/>
    </svg>
    <span>Local Family<br>Owned Business</span>
  </div>

  <div class="abs contact-list">
    <div class="contact"><div class="contact-name">Owen<span class="phone-dot"><svg width="18" height="18" viewBox="0 0 24 24" fill="#e3231c"><path d="M6.6 10.8a15 15 0 0 0 6.6 6.6l2.2-2.2a1 1 0 0 1 1-.25 11.4 11.4 0 0 0 3.6.6 1 1 0 0 1 1 1V20a1 1 0 0 1-1 1A17 17 0 0 1 3 4a1 1 0 0 1 1-1h3.5a1 1 0 0 1 1 1c0 1.25.2 2.45.6 3.6a1 1 0 0 1-.25 1z"/></svg></span></div><span class="contact-number">0491 570 362</span></div>
    <div class="contact"><div class="contact-name">Liam<span class="phone-dot"><svg width="18" height="18" viewBox="0 0 24 24" fill="#e3231c"><path d="M6.6 10.8a15 15 0 0 0 6.6 6.6l2.2-2.2a1 1 0 0 1 1-.25 11.4 11.4 0 0 0 3.6.6 1 1 0 0 1 1 1V20a1 1 0 0 1-1 1A17 17 0 0 1 3 4a1 1 0 0 1 1-1h3.5a1 1 0 0 1 1 1c0 1.25.2 2.45.6 3.6a1 1 0 0 1-.25 1z"/></svg></span></div><span class="contact-number">0491 570 718</span></div>
    <div class="contact"><div class="contact-name">Simon<span class="phone-dot"><svg width="18" height="18" viewBox="0 0 24 24" fill="#e3231c"><path d="M6.6 10.8a15 15 0 0 0 6.6 6.6l2.2-2.2a1 1 0 0 1 1-.25 11.4 11.4 0 0 0 3.6.6 1 1 0 0 1 1 1V20a1 1 0 0 1-1 1A17 17 0 0 1 3 4a1 1 0 0 1 1-1h3.5a1 1 0 0 1 1 1c0 1.25.2 2.45.6 3.6a1 1 0 0 1-.25 1z"/></svg></span></div><span class="contact-number">0491 570 905</span></div>
  </div>

  <div class="abs base-box">
    <div class="region-map" role="img" aria-label="Map of Australia marking the Griffith NSW location"></div>
    <div>
      <div class="base-title">BASED IN GRIFFITH NSW</div>
      <div class="base-sub">Servicing Griffith &amp; surrounds</div>
    </div>
  </div>

  <div class="abs web-row">
    <div class="web-item"><span class="web-icon"><svg width="14" height="10" viewBox="0 0 14 10" fill="none" stroke="#fff" stroke-width="1.5"><rect x=".75" y=".75" width="12.5" height="8.5"/><path d="M.75.75 7 5.5 13.25.75"/></svg></span>Fuel@terradiesel-example.com.au</div>
    <div class="web-item"><span class="web-icon"><svg width="14" height="14" viewBox="0 0 14 14" fill="none" stroke="#fff" stroke-width="1.3"><circle cx="7" cy="7" r="6"/><ellipse cx="7" cy="7" rx="2.6" ry="6"/><line x1="1" y1="7" x2="13" y2="7"/></svg></span>terradiesel-example.com.au</div>
  </div>
</main>
</body>
</html>
```